Business cards to launch an education platform

Hi,
I am looking at having new business cards designed.
I am a startup, developing a web platform for schools and university, the education world. It's an online assessment system.
I would like a card that looks classy, and that is using the colors and the font of my logo.

I have attached:
1) my logo
2) A business card that I have designed quickly so you can have all the information required in the card, but I really don't like it.
3) The font that I am using (Lato Regular) to design my web platform
4) Some screenshots of my web platform so you can have a look at the style that I have.

Target Market(s)

Major market: Education system: Schools and university
Minor markets: Business in general

Industry/Entity Type

Business

Contact Information for Business Card

Clara Fenwick
Director

M: 0437 518 902
E: clara.fenwick@amberLoomSystems.com.au

Requirements
Must have
• The colors of my logo

```html
<!DOCTYPE html>
<html lang="en">
<head>
<meta charset="utf-8">
<title>Amber Loom Systems — Business Cards</title>
<link rel="stylesheet" href="https://fonts.googleapis.com/css2?family=Lato:wght@400&family=Roboto+Condensed:wght@400;700&display=swap">
<style>
  :root {
    --backdrop: #a4a4a4;
    --card-white: #f2f2f2;
    --navy: #0b3868;
    --ink-navy: #12355e;
    --ink-grey: #4a4a4a;
    --brand-blue: #1c5e9e;
    --band-deep: #0a4585;
    --band-mid: #1a62ad;
    --back-text: #e3e6ea;
  }
  * { margin: 0; padding: 0; box-sizing: border-box; }
  html, body { width: 1105px; height: 1200px; overflow: hidden; }
  body { background: var(--backdrop); position: relative; font-family: "Lato", sans-serif; }

  .card { position: absolute; left: 180px; width: 746px; height: 426px; overflow: hidden; }
  .card--front { top: 120px; background: var(--card-white); }
  .card--back { top: 637px; background: var(--navy); }

  .brand { position: absolute; display: flex; flex-direction: column; align-items: center; }
  .brand__mark { width: 58px; height: 58px; background: var(--brand-blue); margin-bottom: 16px; }
  .brand__name { font-family: "Lato", sans-serif; font-weight: 400; text-align: center; letter-spacing: 2px; line-height: 1.2; }
  .card--front .brand { left: 37px; width: 300px; top: 108px; }
  .card--front .brand__name { color: var(--brand-blue); font-size: 27px; }

  .person { position: absolute; left: 342px; top: 108px; }
  .person__name { font-family: "Roboto Condensed", sans-serif; font-weight: 700; font-size: 37px; color: var(--ink-navy); line-height: 1; }
  .person__role { font-family: "Roboto Condensed", sans-serif; font-weight: 700; font-size: 25px; color: var(--ink-grey); margin-top: 8px; }

  .contacts { position: absolute; left: 344px; top: 199px; list-style: none; }
  .contacts__item { display: flex; align-items: center; height: 29px; font-family: "Roboto Condensed", sans-serif; font-size: 17px; color: var(--ink-grey); }
  .contacts__icon { width: 18px; height: 18px; margin-right: 14px; fill: var(--ink-navy); }

  .footer-band {
    position: absolute; left: 0; right: 0; bottom: 0; height: 62px;
    background: linear-gradient(90deg, var(--band-deep) 0%, var(--band-mid) 70%, var(--band-deep) 100%);
  }

  .card--back .brand { left: 0; right: 0; top: 128px; }
  .card--back .brand__mark { background: var(--back-text); }
  .card--back .brand__name { color: var(--back-text); font-size: 34px; }
  .back-url { position: absolute; left: 0; right: 0; top: 357px; text-align: center; font-size: 20px; letter-spacing: 0.5px; color: var(--back-text); }
</style>
</head>
<body>
  <section class="card card--front" aria-label="Business card front">
    <div class="brand">
      <div class="brand__mark"></div>
      <div class="brand__name">AMBER LOOM<br>SYSTEMS</div>
    </div>

    <div class="person">
      <h1 class="person__name">Clara Fenwick</h1>
      <p class="person__role">Director</p>
    </div>

    <ul class="contacts">
      <li class="contacts__item">
        <svg class="contacts__icon" viewBox="0 0 18 18" aria-hidden="true"><path d="M5 1h8a1 1 0 0 1 1 1v14a1 1 0 0 1-1 1H5a1 1 0 0 1-1-1V2a1 1 0 0 1 1-1zm1 2v10h6V3zm3 11.2a.9.9 0 1 0 0 1.8.9.9 0 0 0 0-1.8z"/></svg>
        0437 518 902
      </li>
      <li class="contacts__item">
        <svg class="contacts__icon" viewBox="0 0 18 18" aria-hidden="true"><path d="M1 4h16v10H1zm1.5 1.2L9 10l6.5-4.8V5h-13z"/></svg>
        clara.fenwick@amberLoomSystems.com.au
      </li>
      <li class="contacts__item">
        <svg class="contacts__icon" viewBox="0 0 18 18" aria-hidden="true"><circle cx="9" cy="9" r="7.5"/></svg>
        www.amberLoomSystems.com.au
      </li>
    </ul>

    <div class="footer-band" role="img" aria-label="Decorative blue wave band along the bottom edge"></div>
  </section>

  <section class="card card--back" aria-label="Business card back">
    <div class="brand">
      <div class="brand__mark"></div>
      <div class="brand__name">AMBER LOOM<br>SYSTEMS</div>
    </div>
    <p class="back-url">www.amberLoomSystems.com.au</p>
  </section>
</body>
</html>
```